Brochure for a website accessibility report

This brochure is related to a report that www.qelvantrix.org sell. The report shows the results of an automated audit of a websites accessibility. It shows details of issues found with screen shots, examples of code and provides remediation advice.

The brochure will be a pdf 8.5 inches by 11 inches. It can be anywhere from 6 to 10 pages.

The FlintVue™ name itself should be “Bree Serif” font. The fonts, styles, colors and sizes are up to you.

The images used and logo of the Office of Digital Reachworks and K7P logo are upload

We highlighted in blue page extracts from the report we sell. Do not use the blue highlight, it is merely there to show you where the specific examples of the report we sell are vs the other content in the report. The areas in blue which show the content from the actual report should be shown as an extract of the actual page of the report. You have flexibility to change the layout and the way the content look.

The red square callouts over the blue content are callouts that describe the specific page extracts. We used it as a red callout only so that you would be able to see it. You should change the specific location, look and feel of the callout to be appropriate

Target Market(s)

Marketing and Technical people

Industry/Entity Type

Information Technology

Font styles to use
Sans Serif

Colors

Designer to choose colors to be used in the design.

Requirements
Should not have
• wheelchairs, images of blind people

```html
<!DOCTYPE html>
<html lang="en">
<head>
<meta charset="utf-8">
<title>FlintVue Report Brochure – Pages 6–7</title>
<link href="https://fonts.googleapis.com/css2?family=Bree+Serif&family=Raleway:ital,wght@0,400;0,500;0,700;0,800;1,400;1,600&display=swap" rel="stylesheet">
<style>
  :root {
    --green: #1f9d5c;
    --green-dark: #178a4f;
    --green-light: #5fcf98;
    --mint: #e4f2ea;
    --grey-box: #ececec;
    --ink: #262626;
    --muted: #6a6a6a;
    --rule: #cfcfcf;
    --paper: #fafafa;
    --backdrop: #dcdcdc;
  }
  * { box-sizing: border-box; margin: 0; padding: 0; }
  html, body { width: 1200px; height: 840px; overflow: hidden; }
  body {
    background: var(--backdrop);
    font-family: "Raleway", sans-serif;
    color: var(--ink);
    position: relative;
  }
  .spread {
    position: absolute;
    left: 100px; top: 96px;
    width: 1000px; height: 647px;
    display: flex;
  }
  .page {
    position: relative;
    width: 500px; height: 647px;
    background: var(--paper);
    overflow: hidden;
  }
  .page--left { border-right: 1px solid #e2e2e2; }

  .brand {
    position: absolute; top: 28px;
    display: flex; align-items: center; gap: 6px;
    font-family: "Raleway", sans-serif; font-weight: 800;
    font-size: 7.5px; line-height: 1.1; text-transform: uppercase;
    color: var(--green); width: 110px;
  }
  .brand__square { width: 14px; height: 14px; background: var(--green); flex: none; }
  .page--left .brand { left: 34px; }
  .page--right .brand { right: 34px; justify-content: flex-end; top: 100px; }

  .edition {
    position: absolute; top: 34px;
    font-family: "Raleway", sans-serif; font-style: italic; font-weight: 600;
    font-size: 9px; color: var(--green);
  }
  .page--left .edition { right: 34px; top: 80px; }
  .page--right .edition { left: 40px; }
  .header-rule { position: absolute; height: 1px; background: var(--rule); }

  /* Left page */
  .section-tab {
    position: absolute; left: 34px; top: 68px;
    width: 210px; height: 26px; background: var(--green);
    color: #fff; font-family: "Bree Serif", serif; font-size: 17px;
    padding: 2px 10px; display: flex; justify-content: space-between; align-items: center;
  }
  .section-tab svg { width: 14px; height: 14px; }
  .intro {
    position: absolute; left: 34px; top: 104px; width: 400px;
    font-size: 9.5px; line-height: 1.45;
  }
  .themes {
    position: absolute; left: 34px; right: 34px; top: 158px; height: 116px;
    background: linear-gradient(100deg, var(--green) 40%, var(--green-light));
    padding: 12px 18px; color: #fff; list-style: none;
    font-size: 9.5px; line-height: 1.55;
  }
  .themes li::before { content: "•"; margin-right: 6px; }
  .themes em { font-style: italic; font-weight: 700; }
  .themes span { font-style: italic; }
  .details {
    position: absolute; left: 34px; top: 290px; width: 410px;
    font-size: 9.5px; line-height: 1.45;
  }
  .details p + p { margin-top: 8px; }
  .closing-band {
    position: absolute; left: 0; right: 0; top: 392px; bottom: 0;
    background: var(--green);
  }
  .closing-callout {
    position: absolute; left: 46px; top: 28px; width: 400px; padding: 16px 20px;
    background: linear-gradient(100deg, rgba(255,255,255,0.08), rgba(255,255,255,0.32));
    font-family: "Bree Serif", serif; font-size: 20px; line-height: 1.25; color: #fff;
  }
  .folio {
    position: absolute; bottom: 22px; font-size: 8px;
  }
  .page--left .folio { left: 34px; color: rgba(255,255,255,0.8); }
  .page--right .folio { right: 34px; color: var(--green); }
  .site {
    position: absolute; bottom: 22px; font-size: 9px; font-weight: 700;
  }
  .page--left .site { right: 34px; color: #0f4f2e; }
  .page--right .site { left: 40px; color: var(--ink); }
  .footer-rule { position: absolute; bottom: 26px; height: 1px; }

  /* Right page */
  .topic-title {
    position: absolute; left: 40px; top: 64px;
    font-family: "Bree Serif", serif; font-size: 20px; color: var(--green);
  }
  .topic-lead {
    position: absolute; left: 40px; top: 94px; width: 170px;
    font-weight: 800; font-size: 11px; line-height: 1.35;
  }
  .guidance {
    position: absolute; left: 240px; top: 140px; width: 226px;
    background: var(--mint); padding: 10px 12px; list-style: none;
    font-size: 8.5px; line-height: 1.4; color: var(--muted);
  }
  .guidance li { display: flex; gap: 5px; }
  .guidance li + li { margin-top: 5px; }
  .guidance svg { width: 9px; height: 9px; flex: none; margin-top: 1px; }
  .block-heading {
    position: absolute; left: 40px;
    font-family: "Bree Serif", serif; font-size: 18px; color: var(--green);
  }
  .extract {
    position: absolute; left: 40px; width: 430px;
    background: var(--grey-box); padding-bottom: 12px;
    font-size: 8.5px; line-height: 1.5;
  }
  .extract__band {
    background: var(--green); color: #fff; padding: 6px 12px;
    font-size: 9.5px; line-height: 1.35; margin-bottom: 8px;
  }
  .extract p { padding: 0 12px; }
  .checkpoints { color: var(--green); font-weight: 700; margin-top: 4px; }
  .code { font-family: "Raleway", sans-serif; }
</style>
</head>
<body>
<main class="spread">

  <section class="page page--left" aria-label="Page 6">
    <div class="brand"><span class="brand__square"></span>Office of Digital Reachworks</div>
    <div class="header-rule" style="left:190px; top:42px; width:200px;"></div>
    <p class="edition">2019 Brochure</p>

    <h2 class="section-tab">Section 2
      <svg viewBox="0 0 14 14" aria-hidden="true"><circle cx="7" cy="7" r="7" fill="#fff"/><path d="M4 7.2l2 2 4-4" stroke="var(--green)" stroke-width="1.6" fill="none"/></svg>
    </h2>

    <p class="intro">The next section of the report is designed specifically for your developers and programmers who will be in-the-trenches fixing the actual issues. The issues are prioritized and organized by six themes:</p>

    <ul class="themes">
      <li><em>Media:</em> <span>problems related to imagery, video and plug-ins.</span></li>
      <li><em>Structure:</em> <span>problems related to HTML layout markup and positioning of data.</span></li>
      <li><em>Text:</em> <span>problems related to actual textual content and its comprehension.</span></li>
      <li><em>Scripting:</em> <span>problems related to Scripting, e.g. in JavaScript code.</span></li>
      <li><em>CSS:</em> <span>problems related to Cascading Style Sheets &amp; inline Styles.</span></li>
      <li><em>Form:</em> <span>problems related to Form controls, navigability &amp; comprehension.</span></li>
    </ul>

    <div class="details">
      <p>Within each classification above, we provide specific details about each violation found, which URLs they were present on, code snippets, and screenshots showing you the actual violation.</p>
      <p>Remediation advice is then given to you with resource links and explanations of the guidelines your website doesn’t meet.</p>
    </div>

    <div class="closing-band">
      <p class="closing-callout">The following pages provide six examples of how our FlintVue™ report shows you how to fix the violations based on the classifications listed above.</p>
      <span class="folio">6</span>
      <span class="footer-rule" style="left:60px; width:300px; background:rgba(255,255,255,0.35);"></span>
      <span class="site">www.qelvantrix.org</span>
    </div>
  </section>

  <section class="page page--right" aria-label="Page 7">
    <p class="edition">2019 Brochure</p>
    <div class="header-rule" style="left:150px; top:60px; width:300px;"></div>
    <div class="brand"><span class="brand__square"></span>Office of Digital Reachworks</div>

    <h2 class="topic-title">Media</h2>
    <p class="topic-lead">Ensure that all Media items such as animations/video and audio have an alternative means of understanding the content.</p>

    <ul class="guidance">
      <li><svg viewBox="0 0 10 10" aria-hidden="true"><circle cx="5" cy="5" r="4.2" stroke="var(--green)" fill="none"/><path d="M4 3l2 2-2 2" stroke="var(--green)" fill="none"/></svg>Provide a text alternative for either via a transcript, audio description, sign language, or captioning (open or closed.)</li>
      <li><svg viewBox="0 0 10 10" aria-hidden="true"><circle cx="5" cy="5" r="4.2" stroke="var(--green)" fill="none"/><path d="M4 3l2 2-2 2" stroke="var(--green)" fill="none"/></svg>Additionally, any content provided through an object, Embed, or Applet (or similar 3rd party plugin) must be checked for appropriate keyboard accessible controls.</li>
    </ul>

    <h3 class="block-heading" style="top:236px;">Issue: Image Link Text</h3>
    <div class="extract" style="top:264px;">
      <p class="extract__band">Image ALT attribute text of images within links should not duplicate the text of the link body (link text.)</p>
      <p>Don’t use the same text in an image ALT as the link containing the image. If the link text and the image alt are the same, this creates a “stutter” when screen readers read the content of the link and then the image. When the image doesn’t describe any additional information beyond the link text, authors should set the image alt to "".</p>
      <p class="checkpoints">Issue is relevant to checkpoints: 1.1.1 (A), 2.4.4 (A), 4.1.2 (A)</p>
    </div>

    <h3 class="block-heading" style="top:410px;">General Remediation Advice:</h3>
    <div class="extract" style="top:438px;">
      <p class="extract__band">When dealing with images directly contained within links with link text, don’t use the same text in the image alt text as the link text.</p>
      <p class="code">Before: &lt;a href="products.html"&gt;&lt;img src="products.gif" alt="Products page"/&gt;Products page&lt;/a&gt;</p>
      <p>This leads to a “stutter” as screen readers will read “Products page” twice: once for the image and once for the link. Replace the alt text with "".</p>
      <p class="code">After: &lt;a href="products.html"&gt;&lt;img src="icon.gif" alt="" /&gt;Products page&lt;/a&gt;</p>
    </div>

    <span class="site">www.qelvantrix.org</span>
    <span class="footer-rule" style="left:150px; width:260px; background:var(--rule);"></span>
    <span class="folio">7</span>
  </section>

</main>
</body>
</html>
```